2018 Desk Calendar Design with Better Spine, Better Health with Chiropractic

In conjunction with the Federation of Spinal Wellness Malaysia (FSW), we are organizing a 2018 desk calendar design. The cover page and monthly design size is 210mm (H) x 195mm (W). The will be a total of 27 designs including a cover page (front) [Sample 1], cover page (back) Malaysia National & States Holiday 2018 (https://restdaylist.example.my/2018-dates/) [Sample 2], 12 months design (front) [Sample 3 and 4], 12 months design (back) [Sample 5], Last page (2017 and 2019 calendar) [Sample 6].

Below are some recommendations for monthly back cover design. The main theme remain as Better SPINE, Better HEALTH with CHIROPRACTIC. Each month can in collaborate with of the following element:-

Suggestion 1 (Celebration of the Month)
January - New Year
February - Chinese New Year
March -
April -
May - Labour Day
June - Aidilfitri Festival
July-
August - Independent Day
September - Malaysia Day
October - World Spine Day
November - Deepavali Festival
December - Christmas

Suggestion 2 (States in Malaysia)
January - Perlis
February - Kedah
March - Penang
April - Perak
May - Selangor
June - Negeri Sembilan
July- Melaka
August - Johor
September - Pahang
October - Terengganu
November - Kelantan
December - Sabah & Sarawak

Target Market(s)

Chiropractors and Public

Industry/Entity Type

Chiropractor

Colors

Designer to choose colors to be used in the design.

Requirements
Must have
• The theme for the desk calendar design is Better Spine, Better Health with Chiropractic.
• The cover page should include 5th Anniversary element.
Nice to have
• Lunar or Islamic calendar is optional in the Gregorian calendar.
• AI Format
• Footnote of each page www.spinefsw.example.org

```html
<!DOCTYPE html>
<html lang="en">
<head>
<meta charset="utf-8">
<title>February 2018 – Federation of Spinal Wellness Malaysia Desk Calendar</title>
<link href="https://fonts.googleapis.com/css2?family=Arimo:wght@400;700&family=Great+Vibes&family=PT+Serif:ital@1&display=swap" rel="stylesheet">
<style>
  :root{
    --navy:#262a7c;
    --red:#e0202a;
    --ink:#1d1d1d;
    --grey-col:#e8e8e8;
    --rule:#9a9a9a;
    --quote-bg:rgba(78,78,160,.93);
    --band:#f6d21a;
    --photo-a:#f4f1ee;
    --photo-b:#d9d4cf;
    --photo-c:#bfb5ac;
    --paper:#ffffff;
  }
  *{margin:0;padding:0;box-sizing:border-box}
  html,body{width:1200px;height:1115px;overflow:hidden;background:var(--paper)}
  body{font-family:"Arimo",Arial,sans-serif;color:var(--ink)}
  .page{position:relative;width:1200px;height:1115px;overflow:hidden;background:var(--paper)}

  .binding{position:absolute;top:20px;left:16px;display:flex;gap:27px}
  .binding span{display:block;width:24px;height:24px;background:#111}

  .month-title{position:absolute;left:34px;top:60px;font-family:"Great Vibes",cursive;font-size:118px;color:var(--navy);line-height:1;font-weight:400}
  .title-rule{position:absolute;left:318px;top:156px;width:142px;height:2px;background:var(--navy)}
  .year{position:absolute;left:466px;top:100px;font-size:60px;color:var(--navy);line-height:1}

  .holidays{position:absolute;left:780px;top:100px;width:380px}
  .holidays h2{font-weight:400;font-size:26px;color:var(--red);display:flex;align-items:center;gap:12px}
  .holidays h2::after{content:"";flex:1;height:2px;background:var(--red)}
  .holidays ul{list-style:none;margin-top:20px;font-size:16px;line-height:27.5px}
  .holidays b{color:var(--ink);display:inline-block;margin-right:6px}
  .holidays .name{color:var(--red)}

  .mini{position:absolute;top:276px;width:182px;font-size:9.5px;text-align:center}
  .mini.jan{left:778px}
  .mini.mar{left:972px}
  .mini h3{font-weight:400;font-size:10px;color:var(--navy);margin-bottom:4px}
  .mini .days{display:grid;grid-template-columns:repeat(7,1fr);row-gap:4px}
  .mini .hd{color:var(--navy)}
  .mini .wk{background:var(--grey-col)}

  .grid{position:absolute;left:36px;top:236px;width:708px;display:grid;grid-template-columns:repeat(7,1fr);grid-template-rows:22px repeat(5,79px);column-gap:4px}
  .grid .shade{grid-row:1/7;background:var(--grey-col)}
  .grid .shade.sun{grid-column:1}
  .grid .shade.sat{grid-column:7}
  .dow{grid-row:1;font-size:22px;font-weight:700;color:var(--navy);border-top:2px solid var(--rule);padding:2px 0 0 4px;line-height:20px}
  .day{border-top:2px solid var(--rule);font-size:26px;font-weight:700;padding:8px 0 0 4px;color:var(--ink);position:relative}
  .day.empty{border-top-color:transparent}
  .day.holiday{color:var(--red)}

  .photo{position:absolute;left:0;top:664px;width:1200px;height:451px;
    background:linear-gradient(100deg,var(--photo-b) 0%,var(--photo-a) 35%,#fbfaf8 55%,var(--photo-b) 80%,var(--photo-c) 100%)}

  .quote{position:absolute;left:762px;top:428px;width:438px;height:362px;background:var(--quote-bg);color:#fff;
    font-family:"PT Serif",Georgia,serif;font-style:italic;font-size:29px;line-height:39px;padding:14px 14px 0 14px}

  .contact-band{position:absolute;left:458px;top:978px;width:742px;height:137px;background:var(--band);color:var(--navy);padding:14px 0 0 18px}
  .contact-band .org{font-size:24px;font-weight:700;line-height:28px}
  .contact-band .org-local{font-size:19px;line-height:24px}
  .contact-band .label{font-size:16px;font-weight:700;margin-top:6px}
  .contact-band .lines{font-size:19px;line-height:30px;display:flex;gap:10px;white-space:nowrap;max-width:590px}
  .brand{position:absolute;right:22px;top:14px;width:100px;display:flex;flex-direction:column;align-items:center;gap:6px}
  .brand .dot{width:64px;height:64px;border-radius:50%;background:var(--navy)}
  .brand .mark{font-size:22px;font-weight:700;color:var(--navy);line-height:26px}
</style>
</head>
<body>
<div class="page">
  <div class="binding">
    <span></span><span></span><span></span><span></span><span></span><span></span><span></span><span></span>
    <span></span><span></span><span></span><span></span><span></span><span></span><span></span><span></span>
    <span></span><span></span><span></span><span></span><span></span><span></span><span></span>
  </div>

  <h1 class="month-title">February</h1>
  <div class="title-rule"></div>
  <div class="year">2018</div>

  <section class="holidays">
    <h2>Holidays</h2>
    <ul>
      <li><b>1 Feb</b><span class="name">Federal Territory Day</span></li>
      <li><b>16 Feb</b><span class="name">Chinese New Year</span></li>
      <li><b>17 Feb</b><span class="name">Chinese New Year Holiday</span></li>
      <li><b>18 Feb</b><span class="name">Chinese New Year Holiday</span></li>
    </ul>
  </section>

  <div class="mini jan">
    <h3>January 2018</h3>
    <div class="days">
      <span class="hd">S</span><span class="hd">M</span><span class="hd">T</span><span class="hd">W</span><span class="hd">T</span><span class="hd">F</span><span class="hd">S</span>
      <span class="wk"></span><span>1</span><span>2</span><span>3</span><span>4</span><span>5</span><span class="wk">6</span>
      <span class="wk">7</span><span>8</span><span>9</span><span>10</span><span>11</span><span>12</span><span class="wk">13</span>
      <span class="wk">14</span><span>15</span><span>16</span><span>17</span><span>18</span><span>19</span><span class="wk">20</span>
      <span class="wk">21</span><span>22</span><span>23</span><span>24</span><span>25</span><span>26</span><span class="wk">27</span>
      <span class="wk">28</span><span>29</span><span>30</span><span>31</span><span></span><span></span><span class="wk"></span>
    </div>
  </div>
  <div class="mini mar">
    <h3>March 2018</h3>
    <div class="days">
      <span class="hd">S</span><span class="hd">M</span><span class="hd">T</span><span class="hd">W</span><span class="hd">T</span><span class="hd">F</span><span class="hd">S</span>
      <span class="wk"></span><span></span><span></span><span></span><span>1</span><span>2</span><span class="wk">3</span>
      <span class="wk">4</span><span>5</span><span>6</span><span>7</span><span>8</span><span>9</span><span class="wk">10</span>
      <span class="wk">11</span><span>12</span><span>13</span><span>14</span><span>15</span><span>16</span><span class="wk">17</span>
      <span class="wk">18</span><span>19</span><span>20</span><span>21</span><span>22</span><span>23</span><span class="wk">24</span>
      <span class="wk">25</span><span>26</span><span>27</span><span>28</span><span>29</span><span>30</span><span class="wk">31</span>
    </div>
  </div>

  <div class="grid">
    <div class="shade sun"></div><div class="shade sat"></div>
    <div class="dow" style="grid-column:1">Sun</div><div class="dow" style="grid-column:2">Mon</div><div class="dow" style="grid-column:3">Tue</div><div class="dow" style="grid-column:4">Wed</div><div class="dow" style="grid-column:5">Thu</div><div class="dow" style="grid-column:6">Fri</div><div class="dow" style="grid-column:7">Sat</div>

    <div class="day empty" style="grid-row:2;grid-column:1"></div><div class="day empty" style="grid-row:2;grid-column:2"></div><div class="day empty" style="grid-row:2;grid-column:3"></div><div class="day empty" style="grid-row:2;grid-column:4"></div>
    <div class="day holiday" style="grid-row:2;grid-column:5">1</div><div class="day" style="grid-row:2;grid-column:6">2</div><div class="day" style="grid-row:2;grid-column:7">3</div>

    <div class="day" style="grid-row:3;grid-column:1">4</div><div class="day" style="grid-row:3;grid-column:2">5</div><div class="day" style="grid-row:3;grid-column:3">6</div><div class="day" style="grid-row:3;grid-column:4">7</div><div class="day" style="grid-row:3;grid-column:5">8</div><div class="day" style="grid-row:3;grid-column:6">9</div><div class="day" style="grid-row:3;grid-column:7">10</div>

    <div class="day" style="grid-row:4;grid-column:1">11</div><div class="day" style="grid-row:4;grid-column:2">12</div><div class="day" style="grid-row:4;grid-column:3">13</div><div class="day" style="grid-row:4;grid-column:4">14</div><div class="day" style="grid-row:4;grid-column:5">15</div><div class="day holiday" style="grid-row:4;grid-column:6">16</div><div class="day holiday" style="grid-row:4;grid-column:7">17</div>

    <div class="day holiday" style="grid-row:5;grid-column:1">18</div><div class="day" style="grid-row:5;grid-column:2">19</div><div class="day" style="grid-row:5;grid-column:3">20</div><div class="day" style="grid-row:5;grid-column:4">21</div><div class="day" style="grid-row:5;grid-column:5">22</div><div class="day" style="grid-row:5;grid-column:6">23</div><div class="day" style="grid-row:5;grid-column:7">24</div>

    <div class="day" style="grid-row:6;grid-column:1">25</div><div class="day" style="grid-row:6;grid-column:2">26</div><div class="day" style="grid-row:6;grid-column:3">27</div><div class="day" style="grid-row:6;grid-column:4">28</div><div class="day" style="grid-row:6;grid-column:5"></div><div class="day" style="grid-row:6;grid-column:6"></div><div class="day" style="grid-row:6;grid-column:7"></div>
  </div>

  <div class="photo" role="img" aria-label="Photo of a chiropractor in a white coat pointing at a model of the human spine while explaining it to a patient"></div>

  <p class="quote">The practice of chiropractic focuses on the relationship between structure (primarily the spine) and function (as coordinated by the nervous system) and how that relationship affects the preservation and restoration of health.</p>

  <footer class="contact-band">
    <div class="org">Federation of Spinal Wellness Malaysia</div>
    <div class="org-local">Persekutuan Kesihatan Tulang Belakang Malaysia</div>
    <div class="label">email:</div>
    <div class="lines"><span>enquiry@spinefsw.example.org</span><span>|</span><span>www.spinefsw.example.org</span></div>
    <div class="brand"><span class="dot"></span><span class="mark">FSW</span></div>
  </footer>
</div>
</body>
</html>
```